Print materials for 3-star hotel

We are changing up our print materials (notepads, letterheads, key card jackets, small flyer for the room rates) We are a 3 star business hotel in the Philippines and have mainly used grey tones and clean, simple lines. See attached photos for logo and hotel interior photos.

Target Market(s)

Business

Contact Information for Business Card

Corvale Terrace Hotel
Lindwell Banca Avenue corner Tolenta St Cebu City 6000 Philippines
Tel: +63 32 481 7302
Mobile: +63 917 648 2095
www.corvaleterracehotel.example

Font styles to use
Serif
Sans Serif

Requirements
Must have
• Simple
• Readable font and font size
Nice to have
• Neutral colors, grey and taupes
Should not have
• No purples and bright blues

```html
<!DOCTYPE html>
<html lang="en">
<head>
<meta charset="utf-8">
<title>Corvale Terrace Hotel – Stationery</title>
<link href="https://fonts.googleapis.com/css2?family=Cinzel:wght@400&family=Open+Sans:wght@400&display=swap" rel="stylesheet">
<style>
  :root{
    --bg:#f1f1f1;
    --paper:#fbfbfb;
    --paper-edge:#e2e2e2;
    --ink:#262626;
    --ink-soft:#555;
    --dark:#2b2b2b;
    --rule:#c9c9c9;
    --pen-grey:#a9a9a9;
    --chrome:#dcdcdc;
  }
  *{box-sizing:border-box;margin:0;padding:0}
  html,body{width:1200px;height:1057px;overflow:hidden;background:var(--bg)}
  body{position:relative;font-family:"Open Sans",Arial,sans-serif;color:var(--ink)}
  .piece{position:absolute;background:var(--paper);box-shadow:0 1px 3px rgba(0,0,0,.12)}
  .wordmark{display:flex;flex-direction:column;align-items:center;font-family:"Cinzel",Georgia,serif;font-weight:400;color:var(--ink);text-align:center;line-height:1.1}
  .wordmark .mark-square{background:currentColor;margin-bottom:.35em}
  .wordmark .name{letter-spacing:.14em;white-space:nowrap}
  .wordmark .sub{letter-spacing:.3em}
  .on-dark{color:#f2f2f2}
  .contact{font-size:4.6px;line-height:1.55;color:var(--ink-soft);white-space:nowrap}
  .contact .dot{display:inline-block;width:3px;height:3px;border-radius:50%;background:var(--ink-soft);margin-right:3px;vertical-align:middle}

  /* poster */
  .poster{left:52px;top:42px;width:1116px;height:112px;border-radius:4px}
  .poster .wordmark{position:absolute;left:0;right:0;top:22px}
  .poster .mark-square{width:22px;height:22px}
  .poster .name{font-size:17px}
  .poster .sub{font-size:11px}

  /* notepad */
  .notepad{left:92px;top:196px;width:186px;height:264px}
  .notepad .rings{position:absolute;top:-4px;left:8px;right:8px;display:flex;justify-content:space-between}
  .notepad .rings span{width:5px;height:11px;border:1.5px solid #9a9a9a;border-radius:3px}
  .notepad .wordmark{position:absolute;left:12px;top:30px}
  .notepad .mark-square{width:9px;height:9px}
  .notepad .name{font-size:6px}
  .notepad .sub{font-size:4.5px}
  .notepad .contact{position:absolute;left:112px;top:28px;font-size:3.6px}
  .notepad .lines{position:absolute;left:14px;right:16px;top:76px}
  .notepad .lines span{display:block;height:1px;background:var(--rule);margin-bottom:9.3px}

  /* letterhead */
  .letterhead{left:334px;top:192px;width:370px;height:524px}
  .letterhead .wordmark{position:absolute;left:30px;top:36px}
  .letterhead .mark-square{width:14px;height:14px}
  .letterhead .name{font-size:7.5px}
  .letterhead .sub{font-size:5.5px}
  .letterhead .contact{position:absolute;left:266px;top:33px}

  /* folder */
  .folder{left:728px;top:194px;width:404px;height:551px;background:var(--dark);border-radius:2px}
  .folder .spine{position:absolute;left:348px;top:0;bottom:0;width:2px;background:#6d6d6d}
  .folder .wordmark{position:absolute;left:0;width:350px;top:228px}
  .folder .mark-square{width:34px;height:34px}
  .folder .name{font-size:19px}
  .folder .sub{font-size:12px}

  /* business cards */
  .card-front{left:133px;top:510px;width:146px;height:66px}
  .card-front .wordmark{position:absolute;left:8px;top:19px}
  .card-front .mark-square{width:9px;height:9px}
  .card-front .name{font-size:5.2px}
  .card-front .sub{font-size:4px}
  .card-front .person{position:absolute;left:77px;top:20px;font-size:3.8px;line-height:1.5;color:var(--ink-soft);white-space:nowrap}
  .card-front .person .who{font-family:"Cinzel",Georgia,serif;font-size:5px;color:var(--ink);letter-spacing:.05em}
  .card-back{left:133px;top:628px;width:142px;height:89px;background:var(--dark)}
  .card-back .wordmark{position:absolute;left:0;right:0;top:28px}
  .card-back .mark-square{width:11px;height:11px}
  .card-back .name{font-size:6.2px}
  .card-back .sub{font-size:4.6px}

  /* envelopes */
  .envelope-back{left:188px;top:806px;width:386px;height:193px}
  .envelope-back .wordmark{position:absolute;left:20px;top:18px}
  .envelope-back .mark-square{width:13px;height:13px}
  .envelope-back .name{font-size:6.4px}
  .envelope-back .sub{font-size:4.8px}
  .envelope-back .return{position:absolute;left:22px;top:62px;font-size:5px;line-height:1.4;color:var(--ink-soft)}
  .envelope-front{left:314px;top:750px;width:387px;height:193px}
  .envelope-front .flap{position:absolute;left:0;top:0;width:100%;height:50px;background:var(--dark);border-radius:0 0 6px 6px}
  .envelope-front .flap .wordmark{position:absolute;left:0;right:0;top:10px}
  .envelope-front .flap .mark-square{width:14px;height:14px;margin-bottom:6px}
  .envelope-front .flap .url{font-family:"Open Sans",Arial,sans-serif;font-size:4.5px;letter-spacing:.05em}

  /* pens */
  .pen{position:absolute;left:720px;width:240px;height:10px}
  .pen svg{display:block}
  .pen-white{top:808px}
  .pen-black{top:848px}
  .pen-grey{top:888px}

  /* buttons */
  .badge{position:absolute;width:46px;height:46px;border-radius:50%;background:#fff;box-shadow:0 1px 3px rgba(0,0,0,.18);display:flex;align-items:center;justify-content:center}
  .badge-one{left:594px;top:955px}
  .badge-two{left:663px;top:955px}
  .badge-three{left:733px;top:955px}
  .badge .wordmark .mark-square{width:9px;height:9px}
  .badge .name{font-size:3.6px}
  .badge .sub{font-size:2.8px}
  .badge-plain{width:12px;height:12px;background:var(--ink)}
  .badge-ring{width:34px;height:34px;border-radius:50%;border:1px solid var(--ink)}
</style>
</head>
<body>

<section class="piece poster" aria-label="Poster roll">
  <div class="wordmark"><span class="mark-square"></span><span class="name">CORVALE TERRACE</span><span class="sub">HOTEL</span></div>
</section>

<section class="piece notepad" aria-label="Notepad">
  <div class="rings"><span></span><span></span><span></span><span></span><span></span><span></span><span></span><span></span><span></span><span></span></div>
  <div class="wordmark"><span class="mark-square"></span><span class="name">CORVALE TERRACE</span><span class="sub">HOTEL</span></div>
  <div class="contact">
    Lindwell Banca Avenue corner Tolenta St<br>Cebu City 6000 Philippines<br>
    <span class="dot"></span>+63 32 481 7302<br><span class="dot"></span>+63 917 648 2095<br>
    <span class="dot"></span>www.corvaleterracehotel.example
  </div>
  <div class="lines"><span></span><span></span><span></span><span></span><span></span><span></span><span></span><span></span><span></span><span></span><span></span><span></span><span></span><span></span><span></span><span></span><span></span><span></span><span></span></div>
</section>

<section class="piece letterhead" aria-label="Letterhead">
  <div class="wordmark"><span class="mark-square"></span><span class="name">CORVALE TERRACE</span><span class="sub">HOTEL</span></div>
  <div class="contact">
    Lindwell Banca Avenue corner Tolenta St<br>Cebu City 6000 Philippines<br>
    <span class="dot"></span>+63 32 481 7302<br><span class="dot"></span>+63 917 648 2095<br>
    <span class="dot"></span>marco@corvaleterracehotel.example<br><span class="dot"></span>www.corvaleterracehotel.example
  </div>
</section>

<section class="piece folder" aria-label="Presentation folder">
  <div class="spine"></div>
  <div class="wordmark on-dark"><span class="mark-square"></span><span class="name">CORVALE TERRACE</span><span class="sub">HOTEL</span></div>
</section>

<section class="piece card-front" aria-label="Business card front">
  <div class="wordmark"><span class="mark-square"></span><span class="name">CORVALE TERRACE</span><span class="sub">HOTEL</span></div>
  <div class="person">
    <span class="who">MARCO ADLAWON</span><br>General Manager<br>
    Lindwell Banca Ave cor Tolenta St<br>Cebu City 6000<br>
    +63 32 481 7302<br>+63 917 648 2095<br>www.corvaleterracehotel.example
  </div>
</section>

<section class="piece card-back" aria-label="Business card back">
  <div class="wordmark on-dark"><span class="mark-square"></span><span class="name">CORVALE TERRACE</span><span class="sub">HOTEL</span></div>
</section>

<section class="piece envelope-back" aria-label="Envelope front">
  <div class="wordmark"><span class="mark-square"></span><span class="name">CORVALE TERRACE</span><span class="sub">HOTEL</span></div>
  <p class="return">Lindwell Banca Avenue corner Tolenta St<br>Cebu City 6000 Philippines</p>
</section>

<section class="piece envelope-front" aria-label="Envelope back">
  <div class="flap">
    <div class="wordmark on-dark"><span class="mark-square"></span><span class="url">www.corvaleterracehotel.example</span></div>
  </div>
</section>

<div class="pen pen-white" aria-label="White pen">
  <svg width="240" height="14" viewBox="0 0 240 14"><path d="M0 7 Q10 2 30 2 H96 V12 H30 Q10 12 0 7Z" fill="#fafafa" stroke="#ddd"/><rect x="96" y="2" width="4" height="10" fill="var(--chrome)"/><rect x="100" y="2" width="120" height="10" rx="2" fill="#fafafa" stroke="#ddd"/><rect x="220" y="4" width="14" height="6" rx="2" fill="var(--chrome)"/><rect x="140" y="8" width="70" height="4" rx="2" fill="var(--chrome)"/><rect x="185" y="4" width="5" height="4" fill="var(--ink)"/></svg>
</div>
<div class="pen pen-black" aria-label="Black pen">
  <svg width="240" height="14" viewBox="0 0 240 14"><path d="M0 7 Q10 2 30 2 H96 V12 H30 Q10 12 0 7Z" fill="var(--dark)"/><rect x="96" y="2" width="4" height="10" fill="var(--chrome)"/><rect x="100" y="2" width="120" height="10" rx="2" fill="var(--dark)"/><rect x="220" y="4" width="14" height="6" rx="2" fill="var(--chrome)"/><rect x="140" y="8" width="70" height="4" rx="2" fill="var(--chrome)"/><rect x="185" y="4" width="5" height="4" fill="#fff"/></svg>
</div>
<div class="pen pen-grey" aria-label="Grey pen">
  <svg width="240" height="14" viewBox="0 0 240 14"><path d="M0 7 Q10 2 30 2 H96 V12 H30 Q10 12 0 7Z" fill="var(--pen-grey)"/><rect x="96" y="2" width="4" height="10" fill="var(--chrome)"/><rect x="100" y="2" width="120" height="10" rx="2" fill="var(--pen-grey)"/><rect x="220" y="4" width="14" height="6" rx="2" fill="var(--chrome)"/><rect x="140" y="8" width="70" height="4" rx="2" fill="var(--chrome)"/><rect x="185" y="4" width="5" height="4" fill="#fff"/></svg>
</div>

<div class="badge badge-one" aria-label="Pin badge with name">
  <div class="wordmark"><span class="mark-square"></span><span class="name">CORVALE TERRACE</span><span class="sub">HOTEL</span></div>
</div>
<div class="badge badge-two" aria-label="Pin badge"><span class="badge-plain"></span></div>
<div class="badge badge-three" aria-label="Pin badge with ring"><span class="badge-ring"></span></div>

</body>
</html>
```